SkyvornQ Business Cards and Stationary Design

Need a design for our business cards and stationary. I want to carry on the theme of the logo. I want the business cards to have a design on the back. I would like the business cards and the stationary to carry the same theme, design scheme, and branding

Target Market(s)

Airlines and Maintenance Facilities

Industry/Entity Type

Aviation

Contact Information for Business Card

Name
Position Title
Address: 4827 Trellis Hollow Road, Larkmoor, Westhaven, 34951
Office Number
Mobile Number
Email
Website

Font styles to use
Serif
Sans Serif

Colors

Designer to choose colors to be used in the design.

```html
<!DOCTYPE html>
<html lang="en">
<head>
<meta charset="UTF-8">
<title>SkyvornQ Business Card</title>
<link rel="stylesheet" href="https://fonts.googleapis.com/css2?family=Montserrat:wght@700&family=Lato:ital,wght@0,300;1,300&family=Tinos&display=swap">
<style>
  :root {
    --page: #eeeff1;
    --navy: #0c1d4a;
    --silver: #c9d0e6;
    --paper: #fdfdfd;
    --ink: #1a1f33;
    --line: #1d2340;
    --accent: #1f5fb0;
  }
  * { margin: 0; padding: 0; box-sizing: border-box; }
  html, body {
    width: 1200px; height: 1200px; overflow: hidden;
    background: var(--page);
  }
  .stage {
    position: relative; width: 1200px; height: 1200px;
    display: flex; align-items: center; justify-content: center; gap: 90px;
  }
  .card {
    width: 420px; height: 640px; position: relative; overflow: hidden;
    box-shadow: 0 6px 18px rgba(0,0,0,.12);
  }
  .card--front {
    background: var(--navy);
    display: flex; align-items: center; justify-content: center; gap: 16px;
  }
  .front-mark {
    width: 34px; height: 34px; border-radius: 50%;
    border: 5px solid var(--silver);
  }
  .front-name {
    font-family: "Montserrat", sans-serif; font-weight: 700;
    font-size: 44px; letter-spacing: 3px; color: var(--silver);
  }
  .card--back { background: var(--paper); }
  .back-inner {
    position: absolute; width: 640px; height: 420px;
    left: -110px; top: 110px; transform: rotate(-90deg);
    display: flex; align-items: center;
  }
  .brand {
    width: 250px; flex: none; display: flex; flex-direction: column;
    align-items: center; gap: 20px;
  }
  .brand-mark {
    width: 60px; height: 60px; border-radius: 50%;
    border: 7px solid var(--accent);
  }
  .brand-name {
    font-family: "Montserrat", sans-serif; font-weight: 700;
    font-size: 28px; letter-spacing: 5px; color: var(--navy);
    text-transform: uppercase; white-space: nowrap;
  }
  .divider {
    width: 2px; height: 230px; background: var(--line); flex: none;
  }
  .contact { padding-left: 36px; color: var(--ink); }
  .contact-name {
    font-family: "Lato", sans-serif; font-weight: 300; font-size: 34px;
    white-space: nowrap;
  }
  .contact-role {
    font-family: "Lato", sans-serif; font-style: italic; font-weight: 300;
    font-size: 19px; margin: 4px 0 18px 22px;
  }
  .contact-details {
    font-family: "Tinos", serif; font-size: 16px; line-height: 1.45;
    list-style: none; margin-left: 44px; white-space: nowrap;
  }
</style>
</head>
<body>
<main class="stage">
  <section class="card card--front" aria-label="Business card front">
    <span class="front-mark"></span>
    <span class="front-name">SkyvornQ</span>
  </section>

  <section class="card card--back" aria-label="Business card back">
    <div class="back-inner">
      <div class="brand">
        <span class="brand-mark"></span>
        <span class="brand-name">SkyvornQ</span>
      </div>
      <div class="divider"></div>
      <div class="contact">
        <p class="contact-name">Your Name</p>
        <p class="contact-role">Manager</p>
        <ul class="contact-details">
          <li>P: 555.014.3064</li>
          <li>P: 555.014.3064</li>
          <li>W: www.skyvornq.com</li>
          <li>E: yourname@skyvornq.com</li>
          <li>4827 Trellis Hollow Road,</li>
          <li>Larkmoor, Westhaven, 34951</li>
        </ul>
      </div>
    </div>
  </section>
</main>
</body>
</html>
```